Veldmark Supplies Business Card

Professional business card that stand out to our potential customers. Front and back with clean modern design

Industry/Entity Type

Oil and gas

Contact Information for Business Card

Name, address, website , office phone and cell number

Requirements
Must have
• Editable files for each employee

```html
<!DOCTYPE html>
<html lang="en">
<head>
<meta charset="utf-8">
<title>Veldmark Supplies Business Card</title>
<link href="https://fonts.googleapis.com/css2?family=Montserrat:wght@400;500;800&display=swap" rel="stylesheet">
<style>
  :root {
    --page: #1b1b1c;
    --card: #2b2b2d;
    --red: #ed1c24;
    --blue: #1fb3d6;
    --white: #f4f4f4;
    --muted: #d9d9d9;
    --pattern-light: #8e8e90;
    --pattern-dark: #111112;
  }
  * { box-sizing: border-box; margin: 0; padding: 0; }
  html, body { width: 1200px; height: 880px; overflow: hidden; }
  body {
    background: var(--page);
    font-family: "Montserrat", Arial, sans-serif;
    color: var(--white);
    position: relative;
  }
  .card {
    position: absolute;
    left: 250px;
    width: 700px;
    height: 400px;
    background: var(--card);
    box-shadow: 0 12px 30px rgba(0,0,0,.55);
    overflow: hidden;
  }
  .card--back { top: 20px; }
  .card--front { top: 460px; }

  /* back side */
  .back-pattern {
    position: absolute;
    inset: 0;
    background: linear-gradient(110deg, var(--pattern-light) 0%, #4a4a4c 45%, var(--pattern-dark) 100%);
    opacity: .55;
  }
  .back-mark {
    position: absolute;
    right: 150px;
    top: 178px;
    display: flex;
    align-items: center;
    gap: 8px;
    font-weight: 800;
    font-size: 15px;
    letter-spacing: .04em;
    text-transform: uppercase;
    color: var(--red);
  }
  .back-mark__square { width: 12px; height: 12px; background: var(--red); }

  /* front side */
  .brand {
    position: absolute;
    left: 40px;
    top: 160px;
    width: 250px;
    display: flex;
    align-items: center;
    gap: 12px;
  }
  .brand__square { width: 34px; height: 34px; background: var(--blue); flex: none; }
  .brand__name {
    font-weight: 800;
    font-size: 26px;
    line-height: 1.1;
    text-transform: uppercase;
    color: var(--red);
  }
  .divider {
    position: absolute;
    left: 318px;
    top: 50px;
    width: 2px;
    height: 300px;
    background: var(--red);
  }
  .details {
    position: absolute;
    left: 345px;
    top: 46px;
    width: 330px;
  }
  .details__name {
    font-weight: 800;
    font-size: 27px;
    letter-spacing: .01em;
    text-transform: uppercase;
    color: var(--red);
    line-height: 1.1;
  }
  .details__role { font-size: 17px; color: var(--muted); margin-top: 4px; }
  .details__address { font-size: 16px; line-height: 1.35; margin-top: 18px; }
  .contacts { list-style: none; margin-top: 18px; }
  .contacts li {
    display: flex;
    align-items: center;
    gap: 12px;
    font-size: 16px;
    line-height: 1;
    margin-bottom: 12px;
  }
  .contacts__icon {
    width: 22px;
    height: 22px;
    background: var(--red);
    display: flex;
    align-items: center;
    justify-content: center;
    flex: none;
  }
  .contacts__icon svg { width: 14px; height: 14px; }
</style>
</head>
<body>

<section class="card card--back" aria-label="Card back">
  <div class="back-pattern" role="img" aria-label="Repeating brand monogram pattern fading from light grey to black"></div>
  <div class="back-mark"><span class="back-mark__square"></span>Veldmark Supplies</div>
</section>

<section class="card card--front" aria-label="Card front">
  <div class="brand">
    <span class="brand__square"></span>
    <span class="brand__name">Veldmark<br>Supplies</span>
  </div>

  <div class="divider"></div>

  <div class="details">
    <h1 class="details__name">Dario Whitcombe</h1>
    <p class="details__role">President</p>
    <p class="details__address">2240 Harlow Ave, Ste<br>100, Dalton, TX 75204</p>
    <ul class="contacts">
      <li>
        <span class="contacts__icon"><svg viewBox="0 0 14 14"><path d="M2 4c0-2 3-3 5-3s5 1 5 3v1H9V4H5v1H2z M3 6h8l1 6H2z" fill="#fff"/></svg></span>
        555-014-2273
      </li>
      <li>
        <span class="contacts__icon"><svg viewBox="0 0 14 14"><rect x="4" y="1" width="6" height="12" rx="1" fill="none" stroke="#fff" stroke-width="1.4"/><circle cx="7" cy="11" r=".8" fill="#fff"/></svg></span>
        000-000-9999
      </li>
      <li>
        <span class="contacts__icon"><svg viewBox="0 0 14 14"><rect x="1" y="3" width="12" height="8" fill="#fff"/><path d="M1 3l6 5 6-5" fill="none" stroke="#ed1c24" stroke-width="1.2"/></svg></span>
        info@example-youremail.com
      </li>
      <li>
        <span class="contacts__icon"><svg viewBox="0 0 14 14"><circle cx="7" cy="7" r="5.5" fill="none" stroke="#fff" stroke-width="1.3"/><path d="M1.5 7h11M7 1.5c-2.5 3-2.5 8 0 11M7 1.5c2.5 3 2.5 8 0 11" fill="none" stroke="#fff" stroke-width="1"/></svg></span>
        www.example-yourwebsite.com
      </li>
    </ul>
  </div>
</section>

</body>
</html>
```